Coupon/promo code site

I am looking for a one page website that will provide a list of coupon codes that are used at checkout when buying something online. The site will only have coupon codes for one online retailer. I would like this to be generic (i.e. not specific to any one retailer). I would like to have some interchangeable parts so that I could later customize the site so that it is specific to any given retailer.

I envision the site having a list of coupon codes with information about each code like when it expires and what it provides. For example there would be a: code, expiration date, short description or name, and a longer description (i.e. details).
Updates

Project Deadline Extended
Reason: I am going to submit a wire frame that provides a better idea of what I am looking for.

I have uploaded a wire frame that gives a more clear indication of what I am looking for.  Please see this before submitting designs.  If you have already submitted a design, please revise your design considering the wire frame I have provided.

Thanks,
Brent

Target Market(s)

Someone who is shopping online and searching for a specific retailers coupon codes

Industry/Entity Type

Coupon

Requirements
Must have
• I would like the site to have a white or light colored background.

I need a place or two where I can interchangeably place different retailers' logos.

The web page should have a title like, "[retailer's] online coupon code"

In addition to a list or table of coupon codes, there should below this be a list or table of special offers or sale items.

At the very bottom in a way that is not too noticeable, it should say, "This coupon site was created by Pelvo Deals."

There should be a section (probably on the right side) that allows a user to submit their email address to be notified in the future of specials/deals for this retailer.

There should be a nice looking link that goes to the online retailer's website.
Nice to have
• Example sites with a look and feel that I like are:

http://www.quorvane.com/
https://thebrattle.com/
http://www.plimworks.com

This is an example of a site with coupon codes for just one retailer. This site is a little too busy, but you get the idea:
www.makenforth.com/coupon-codes‎

```html
<!DOCTYPE html>
<html lang="en">
<head>
<meta charset="utf-8">
<title>Company Name Coupon Codes</title>
<link rel="stylesheet" href="https://fonts.googleapis.com/css2?family=Jost:wght@700&family=Open+Sans:wght@400&family=Arimo:wght@400;700&family=Oswald:wght@500&display=swap">
<style>
:root{
  --brand-red:#e8201f;
  --title-blue:#1477b5;
  --bar-blue:#0a8ed3;
  --panel-grey:#e1e1e1;
  --side-grey:#e4e4e4;
  --code-dark:#555555;
  --code-hover:#8a8a8a;
  --text-dark:#333333;
  --text-mid:#555555;
  --expire-red:#e0302b;
  --icon-grey:#8a8a8a;
  --white:#ffffff;
}
*{box-sizing:border-box;margin:0;padding:0}
html,body{width:1200px;height:1007px;overflow:hidden;background:var(--white)}
.page{position:relative;width:980px;height:822px;transform:scale(1.22449);transform-origin:0 0;font-family:"Arimo",Arial,sans-serif;color:var(--text-dark)}
.abs{position:absolute}

.retailer-name{left:24px;top:9px;height:66px;display:flex;align-items:center;font-family:"Arimo",Arial,sans-serif;font-weight:700;font-size:28px;color:var(--text-dark)}
.site-title{left:284px;top:14px;font-family:"Jost",sans-serif;font-weight:700;font-size:45px;letter-spacing:0;color:var(--title-blue);line-height:1.2;white-space:nowrap}
.rule{left:0;width:980px;border-top:1px dashed #c9c9c9}
.welcome{left:0;top:98px;width:980px;text-align:center;font-family:"Open Sans",sans-serif;font-size:27.5px;line-height:36px;color:var(--text-dark)}

.coupons{left:9px;top:235px;width:691px;height:459px;background:var(--panel-grey);border-radius:14px}
.section-bar{position:absolute;left:8px;top:7px;width:674px;height:40px;background:var(--bar-blue);border-radius:10px}
.section-bar::after{content:"";position:absolute;inset:3px;border:1px dashed rgba(255,255,255,.85);border-radius:8px}
.section-bar h2{position:absolute;left:17px;top:8px;font-family:"Jost",sans-serif;font-weight:700;font-size:19px;color:var(--white);letter-spacing:.3px}

.coupon{position:absolute;left:10px;width:670px;height:90px;background:var(--white);border-radius:10px}
.coupon-name{position:absolute;left:18px;top:13px;font-size:18px}
.coupon-detail{position:absolute;left:18px;top:37px;font-size:12.3px;color:var(--text-dark)}
.coupon-expiry{position:absolute;left:18px;top:61px;font-size:14.5px;color:var(--expire-red)}
.code-label{position:absolute;right:142px;top:13px;font-size:17px}
.code-button{position:absolute;left:537px;top:11px;width:119px;height:28px;border-radius:8px;background:var(--code-dark);color:var(--white);font-family:"Jost",sans-serif;font-weight:700;font-size:14px;letter-spacing:.8px;text-align:center;line-height:28px}
.code-button.is-revealed{background:var(--code-hover)}
.copy-tip{position:absolute;left:534px;top:46px;width:125px;height:25px;border-radius:9px;background:var(--brand-red);color:var(--white);font-size:12px;text-align:center;line-height:25px;z-index:2}
.copy-tip::before{content:"";position:absolute;left:44px;top:-7px;border:7px solid transparent;border-left-color:var(--brand-red);border-bottom-color:var(--brand-red);border-top:0}
.copy-tip b{font-weight:700}
.cursor{position:absolute;left:637px;top:20px;z-index:3}
.shop-at{position:absolute;right:19px;top:63px;font-size:13.8px;color:var(--text-dark)}
.shop-at b{margin-left:3px}

.newsletter{left:720px;top:235px;width:246px;height:279px;background:var(--side-grey)}
.side-head{position:absolute;left:0;width:246px;background:var(--bar-blue);border-top:1px dashed rgba(255,255,255,.9);border-bottom:1px dashed rgba(255,255,255,.9)}
.newsletter .side-head{top:8px;height:87px}
.mail-icon{position:absolute;left:23px;top:16px}
.newsletter h3{position:absolute;left:105px;top:17px;font-family:"Oswald",sans-serif;font-weight:500;font-size:19.5px;line-height:24px;color:var(--white)}
.newsletter p{position:absolute;left:12px;top:114px;width:222px;text-align:center;font-size:12px;line-height:14.5px;color:var(--text-mid)}
.email-field{position:absolute;left:10px;top:190px;width:226px;height:26px;background:var(--white);border:1px solid #cfcfcf;border-radius:5px;font-size:11px;padding-left:11px;line-height:24px;color:#222}
.subscribe{position:absolute;left:11px;top:226px;width:107px;height:33px;border-radius:5px;background:linear-gradient(#3fa7e6,#1279bf);border:2px solid #d6d6d6;color:var(--white);font-family:"Oswald",sans-serif;font-weight:500;font-size:18px;text-align:center;line-height:28px}

.share{left:720px;top:535px;width:246px;height:119px;background:var(--side-grey)}
.share .side-head{top:7px;height:46px}
.share h3{text-align:center;font-family:"Oswald",sans-serif;font-weight:500;font-size:22px;line-height:44px;color:var(--white)}
.social{position:absolute;left:25px;top:62px;display:flex;gap:7px}
.social span{width:43px;height:43px;background:var(--icon-grey)}

.footer{left:0;top:725px;width:980px;height:83px;background:var(--side-grey);text-align:center}
.footer .copyright{margin-top:24px;font-size:12px;color:#333}
.footer .credit{margin-top:6px;font-size:11px;color:#8a8a8a}
</style>
</head>
<body>
<div class="page">
  <div class="abs retailer-name">Brightmart</div>
  <h1 class="abs site-title">Company Name Coupon Codes</h1>
  <div class="abs rule" style="top:87px"></div>
  <p class="abs welcome">Welcome to the Company Name coupon page.<br>Here you will find the best and most up to date coupon codes<br>available directly from Company name</p>
  <div class="abs rule" style="top:218px"></div>

  <section class="abs coupons">
    <div class="section-bar"><h2>Featured Coupon Codaes</h2></div>

    <article class="coupon" style="top:58px">
      <div class="coupon-name">$51.26 Average savings on Brightmart.com</div>
      <div class="coupon-detail">Receive up to 60% off + Extra 20% off Select Jewelry &amp; Watches.</div>
      <div class="coupon-expiry">Offer Expires: Aug 24, 2013</div>
      <div class="code-label">Coupon Code:</div>
      <div class="code-button is-revealed">12FOR12</div>
      <svg class="cursor" width="18" height="22" viewBox="0 0 18 22"><path d="M5 1.5c1 0 1.6.7 1.6 1.6v7l.6-.2c.9-.3 1.7.1 2 .9.9-.4 1.8 0 2.1.8.9-.3 1.8.2 2 1 .9-.2 1.7.4 1.7 1.3v3.5c0 2.6-2 4.6-4.6 4.6H8.3c-1.3 0-2.4-.6-3.100-1.6L1.4 15c-.6-.8-.3-1.9.6-2.3.6-.3 1.300-.1 1.8.4l.6.7V3.1c0-.9.6-1.6 1.6-1.6z" fill="#fff" stroke="#222" stroke-width="1.2"/></svg>
      <div class="copy-tip"><b>Click</b> to copy code</div>
      <div class="shop-at">Use this code when shopping at : <b>Brightmart.com</b></div>
    </article>

    <article class="coupon" style="top:158px">
      <div class="coupon-name">Free Shipping</div>
      <div class="coupon-detail">Receive up to 60% off + Extra 20% off Select Jewelry &amp; Watches.</div>
      <div class="coupon-expiry">Offer Expires: Aug 24, 2013</div>
      <div class="code-label">Coupon Code:</div>
      <div class="code-button"></div>
      <div class="shop-at">Use this code when shopping at : <b>Brightmart.com</b></div>
    </article>

    <article class="coupon" style="top:258px">
      <div class="coupon-name">$51.26 Average savings on Brightmart.com</div>
      <div class="coupon-detail">Receive up to 60% off + Extra 20% off Select Jewelry &amp; Watches.</div>
      <div class="coupon-expiry">Offer Expires: Aug 24, 2013</div>
      <div class="code-label">Coupon Code:</div>
      <div class="code-button"></div>
      <div class="shop-at">Use this code when shopping at : <b>Brightmart.com</b></div>
    </article>

    <article class="coupon" style="top:358px">
      <div class="coupon-name">Free Shipping</div>
      <div class="coupon-detail">Receive up to 60% off + Extra 20% off Select Jewelry &amp; Watches.</div>
      <div class="coupon-expiry">Offer Expires: Aug 24, 2013</div>
      <div class="code-label">Coupon Code:</div>
      <div class="code-button"></div>
      <div class="shop-at">Use this code when shopping at : <b>Brightmart.com</b></div>
    </article>
  </section>

  <aside class="abs newsletter">
    <div class="side-head">
      <svg class="mail-icon" width="60" height="50" viewBox="0 0 60 50">
        <path d="M2 20 L30 2 L58 20 V48 H2 Z" fill="#fff"/>
        <rect x="12" y="10" width="36" height="26" fill="#0a8ed3"/>
        <rect x="19" y="16" width="22" height="3" fill="#fff"/>
        <rect x="19" y="22" width="22" height="3" fill="#fff"/>
        <path d="M2 20 L30 38 L58 20 V48 H2 Z" fill="#fff" stroke="#0a8ed3" stroke-width="2"/>
        <path d="M2 48 L24 32 M58 48 L36 32" stroke="#0a8ed3" stroke-width="2"/>
      </svg>
      <h3>Never Miss<br>Another Deal!</h3>
    </div>
    <p>Our coupons are updated frequently, so be sure to sign-up for our newsletter to receive notification of new coupon codes and exclusive offers.</p>
    <div class="email-field">Enter Your Email Address Here</div>
    <div class="subscribe">subscribe</div>
  </aside>

  <aside class="abs share">
    <div class="side-head"><h3>share this site</h3></div>
    <div class="social"><span></span><span></span><span></span><span></span></div>
  </aside>

  <footer class="abs footer">
    <p class="copyright">Copyright © 2013 couponhaven.com All rights reserved.</p>
    <p class="credit">This coupon site was created by Pelvo Deals</p>
  </footer>
</div>
</body>
</html>
```